This book will apply the 12 Steps to gaming addiction, also known as video game addiction. The primary purpose of the book is to provide an effective solution for this new type of addiction. The solution is based on the rich and successful concepts of traditional twelve-step programs like RQ.

The title on the cover will be "Nine Doors Out of the Endless Level" and "by Peter Halvorn". A subtitle can be used if it works in your design of "A Practical Path Back from Compulsive Screen Play". Cover will be for a 6" x 9" book approximately 110 pages in length.

Some back cover text including some review quotes and an author bio are in the attached Word doc. There is also an author photo attached for for the back cover.

Requirements
Must have
• For the cover design it could be stylized, or an image, a partial image, or whatever. I am open to suggestions. Think about what would be noticed by a person searching for help with moderating their video game use, or by the parents or loved ones of problem gamers. Something contemporary and eye catching.

```html
<!DOCTYPE html>
<html lang="en">
<head>
<meta charset="utf-8">
<title>Nine Doors Out of the Endless Level — Cover</title>
<link rel="stylesheet" href="https://fonts.googleapis.com/css2?family=Saira+Extra+Condensed:wght@500;600;700&family=Poppins:wght@400;500;600&display=swap">
<style>
  :root {
    --stage: #e7e4df;
    --cover-black: #050608;
    --orange: #f4925f;
    --orange-deep: #ee7d52;
    --orange-light: #f8a97e;
    --blue-grey: #8796c8;
    --blue-light: #b0bce6;
    --white: #f4f4f6;
    --rule: #7f8fc4;
  }
  * { margin: 0; padding: 0; box-sizing: border-box; }
  html, body {
    width: 1200px; height: 1000px; overflow: hidden;
    background: var(--stage);
  }
  .stage { position: relative; width: 1200px; height: 1000px; }

  .cover {
    position: absolute; left: 300px; top: 50px;
    width: 600px; height: 900px;
    background: var(--cover-black);
    overflow: hidden;
    box-shadow: 0 10px 30px rgba(0,0,0,.25);
  }

  .cover-photo {
    position: absolute; inset: 0;
    background:
      radial-gradient(circle at 82% 60%, rgba(255,255,255,.95) 0 30px, rgba(255,255,255,0) 60px),
      radial-gradient(ellipse 150px 90px at 66% 64%, rgba(214,60,120,.8), rgba(214,60,120,0) 100%),
      radial-gradient(ellipse 240px 280px at 72% 82%, rgba(52,80,190,.9), rgba(52,80,190,0) 100%),
      radial-gradient(ellipse 180px 110px at 58% 48%, rgba(31,143,168,.45), rgba(31,143,168,0) 100%),
      radial-gradient(ellipse 130px 110px at 48% 70%, rgba(190,60,80,.4), rgba(190,60,80,0) 100%),
      linear-gradient(180deg, var(--cover-black) 0%, var(--cover-black) 38%, #0b1130 66%, #101a46 100%);
  }

  .cover-type { position: absolute; inset: 0; }
  .cover-type text {
    font-family: "Saira Extra Condensed", "Arial Narrow", sans-serif;
    text-transform: uppercase;
  }
  .word-small { font-weight: 600; fill: var(--white); }
  .word-orange { font-weight: 600; fill: url(#orangeFade); }
  .word-blue { font-weight: 500; fill: url(#blueFade); }
  .author-name { font-weight: 600; fill: var(--orange); }

  .title { position: absolute; inset: 0; font-size: 0; }

  .endorsement {
    position: absolute; left: 66px; top: 440px; width: 180px;
    font-family: "Poppins", Arial, sans-serif; color: var(--white);
  }
  .endorsement .quote { font-size: 15px; font-weight: 500; line-height: 1.5; }
  .endorsement .source { margin-top: 12px; font-size: 14px; font-weight: 600; color: var(--blue-grey); text-transform: uppercase; line-height: 1.3; }
  .endorsement .role { font-size: 13.5px; font-weight: 400; line-height: 1.35; color: #e8e8ee; }
</style>
</head>
<body>
<main class="stage">
  <article class="cover">
    <div class="cover-photo" role="img" aria-label="Photo of a young person in a VR headset glowing with blue and magenta light, falling code streams behind"></div>

    <h1 class="title" aria-label="Nine Doors Out of the Endless Level">
      <svg class="cover-type" width="600" height="900" viewBox="0 0 600 900" aria-hidden="true">
        <defs>
          <linearGradient id="orangeFade" x1="0" y1="0" x2="0" y2="1">
            <stop offset="0" stop-color="var(--orange-light)"/>
            <stop offset="1" stop-color="var(--orange-deep)"/>
          </linearGradient>
          <linearGradient id="blueFade" x1="0" y1="0" x2="1" y2="0">
            <stop offset="0" stop-color="var(--blue-light)"/>
            <stop offset="1" stop-color="var(--blue-grey)"/>
          </linearGradient>
        </defs>

        <g class="title-rule" stroke="var(--rule)" stroke-width="1.5" fill="none">
          <line x1="63" y1="72" x2="78" y2="72"/>
          <line x1="160" y1="72" x2="222" y2="72"/>
          <line x1="222" y1="72" x2="222" y2="410"/>
          <line x1="222" y1="112" x2="250" y2="112"/>
        </g>
        <g fill="var(--rule)">
          <circle cx="256" cy="112" r="9"/>
          <circle cx="222" cy="410" r="9"/>
        </g>

        <text class="word-small" x="82" y="92" font-size="44" textLength="74" lengthAdjust="spacingAndGlyphs">Nine</text>
        <text class="word-orange" x="64" y="280" font-size="190" textLength="140" lengthAdjust="spacingAndGlyphs">Doors</text>
        <text class="word-small" x="64" y="388" font-size="72" textLength="140" lengthAdjust="spacingAndGlyphs">Out of</text>

        <text class="word-small" x="244" y="192" font-size="52" textLength="56" lengthAdjust="spacingAndGlyphs">The</text>
        <text class="word-blue" x="308" y="192" font-size="96" textLength="232" lengthAdjust="spacingAndGlyphs">Endless</text>
        <text class="word-orange" x="242" y="404" font-size="250" textLength="298" lengthAdjust="spacingAndGlyphs">Level</text>

        <text class="author-name" x="62" y="850" font-size="104" textLength="476" lengthAdjust="spacingAndGlyphs">Peter Halvorn</text>
      </svg>
    </h1>

    <blockquote class="endorsement">
      <p class="quote">“A must-read for<br>anyone who is<br>addicted to or<br>thinks they may<br>have a problem<br>with digital gaming...”</p>
      <p class="source">Dale Whitcombe</p>
      <p class="role">Noted Interventionist<br>and Keynote Speaker</p>
    </blockquote>
  </article>
</main>
</body>
</html>
```